Business Card Design for Property Development Company Director

I am looking for a professional and unforgettable business card design for our Director of our Property Development Company.
Please see attached .pptx file to find out what information to include. You don't have to follow the exact format shown in the file - I am interested to see your creative flair using the information provided.

```html
<!DOCTYPE html>
<html lang="en">
<head>
<meta charset="utf-8">
<title>Kelmont Property Group – Business Card</title>
<link href="https://fonts.googleapis.com/css2?family=Lato:wght@400;700;900&display=swap" rel="stylesheet">
<style>
  :root {
    --backdrop: #2f2f2f;
    --card-white: #ffffff;
    --brand-blue: #0d57a6;
    --brand-grey: #666666;
    --text-grey: #444444;
    --rule-grey: #9a9a9a;
  }
  html, body {
    margin: 0;
    padding: 0;
    width: 1200px;
    height: 1200px;
    overflow: hidden;
    background: var(--backdrop);
    font-family: "Lato", sans-serif;
  }
  .canvas {
    position: relative;
    width: 1200px;
    height: 1200px;
  }
  .card {
    position: absolute;
    top: 310px;
    height: 594px;
    overflow: hidden;
  }
  .card-front {
    left: 234px;
    width: 364px;
    background: var(--card-white);
  }
  .card-back {
    left: 627px;
    width: 369px;
    background: var(--brand-blue);
  }

  /* Front */
  .brand {
    position: absolute;
    left: 32px;
    top: 145px;
    display: flex;
    align-items: center;
    gap: 14px;
    color: var(--brand-blue);
    font-weight: 700;
  }
  .brand-square {
    width: 62px;
    height: 62px;
    background: var(--brand-grey);
  }
  .brand-name { line-height: 1; }
  .brand-name .word {
    display: block;
    font-size: 43px;
    letter-spacing: 0.5px;
  }
  .brand-name .sub {
    display: block;
    font-size: 15px;
    letter-spacing: 3.6px;
    margin-top: 6px;
  }
  .person {
    position: absolute;
    left: 0;
    right: 0;
    top: 340px;
    text-align: center;
  }
  .person-name {
    color: var(--brand-blue);
    font-weight: 700;
    font-size: 22px;
    margin: 0;
    line-height: 1.2;
  }
  .person-role {
    color: var(--text-grey);
    font-size: 17px;
    margin: 0;
    line-height: 1.2;
  }
  .icon-row {
    position: absolute;
    left: 87px;
    top: 395px;
  }
  .contact {
    position: absolute;
    left: 0;
    right: 0;
    top: 427px;
    text-align: center;
    color: var(--text-grey);
    font-size: 17px;
    line-height: 22px;
  }
  .contact p { margin: 0; }
  .rule {
    position: absolute;
    left: 88px;
    width: 195px;
    top: 507px;
    height: 1px;
    background: var(--rule-grey);
  }
  .licence {
    position: absolute;
    left: 0;
    right: 0;
    top: 527px;
    text-align: center;
    color: var(--text-grey);
    font-size: 17px;
    margin: 0;
  }

  /* Back */
  .back-top {
    position: absolute;
    left: 0;
    top: 0;
    width: 100%;
    height: 312px;
    background: var(--brand-grey);
  }
  .tagline {
    position: absolute;
    left: 0;
    right: 0;
    text-align: center;
    color: var(--card-white);
    font-size: 17px;
    line-height: 21px;
    margin: 0;
  }
  .tagline-top { top: 48px; }
  .tagline-bottom { top: 507px; }
  .back-mark {
    position: absolute;
    left: 0;
    right: 0;
    top: 150px;
    display: flex;
    flex-direction: column;
    align-items: center;
    gap: 22px;
  }
  .back-square {
    width: 118px;
    height: 118px;
    background: var(--card-white);
  }
  .back-name {
    color: var(--card-white);
    font-weight: 900;
    font-size: 66px;
    line-height: 1;
    letter-spacing: 1px;
    margin: 0;
  }
</style>
</head>
<body>
<main class="canvas">

  <section class="card card-front" aria-label="Business card front">
    <div class="brand">
      <span class="brand-square"></span>
      <span class="brand-name">
        <span class="word">KELMONT</span>
        <span class="sub">PROPERTY GROUP</span>
      </span>
    </div>

    <div class="person">
      <h1 class="person-name">DANIEL MARSH</h1>
      <p class="person-role">Director</p>
    </div>

    <svg class="icon-row" width="190" height="24" viewBox="0 0 190 24" aria-hidden="true">
      <line x1="0" y1="12" x2="54" y2="12" stroke="#9a9a9a" stroke-width="1"/>
      <line x1="136" y1="12" x2="190" y2="12" stroke="#9a9a9a" stroke-width="1"/>
      <circle cx="67" cy="12" r="11.5" fill="#0d57a6"/>
      <path d="M61 9.5 q6 -4 12 0 l-1.5 2 h-2 l-0.5 -1.5 h-4 l-0.5 1.5 h-2 z M62.5 12.5 h9 v4 h-9 z" fill="#fff"/>
      <circle cx="94" cy="12" r="11.5" fill="#0d57a6"/>
      <rect x="88" y="8" width="12" height="8.5" fill="#fff"/>
      <path d="M88 8 l6 5 l6 -5" fill="none" stroke="#0d57a6" stroke-width="1.2"/>
      <circle cx="122" cy="12" r="11.5" fill="#0d57a6"/>
      <circle cx="122" cy="12" r="6" fill="none" stroke="#fff" stroke-width="1.4"/>
      <ellipse cx="122" cy="12" rx="2.6" ry="6" fill="none" stroke="#fff" stroke-width="1.1"/>
      <line x1="116" y1="12" x2="128" y2="12" stroke="#fff" stroke-width="1.1"/>
    </svg>

    <div class="contact">
      <p>0400 318 562</p>
      <p>daniel@kelmont.com.au</p>
      <p>www.kelmont.com.au</p>
    </div>

    <div class="rule"></div>
    <p class="licence">Real Estate Lic:&nbsp; 5207316 &amp; 5207317</p>
  </section>

  <section class="card card-back" aria-label="Business card back">
    <div class="back-top"></div>
    <p class="tagline tagline-top">PROPERTY DEVELOPMENT<br>&amp; SITE ACQUISITION SPECIALISTS</p>
    <div class="back-mark">
      <span class="back-square"></span>
      <p class="back-name">KELMONT</p>
    </div>
    <p class="tagline tagline-bottom">Ask me about our INVESTMENT<br>&amp; PARTNERSHIP opportunities</p>
  </section>

</main>
</body>
</html>
```